Emerging automotive detailing business

I am starting a small automotive detailing business in hopes of becoming a well-known detailer to work on high end cars. I would like a card to reflect the high quality and time I put into my work. The name of the company is Bright Crest Detailing. I feel like it represents racecars getting off the line at the drag strip as well as an innuendo of "Up the Ladder". I do minor paint correction such as clay barring, multi-step buffing and polishing, waxing, hand washes, etc. I am always striving to learn more and improve my work. My goal is to have total customer satisfaction. This is a female run business but I do not want it to be very girly. Elegant is okay! I have pictures of my personal wrenfield attached, they do not need to be incorporated but if you can think of a cool way to use 1 or all of them, go for it!

Target Market(s)

Anyone that owns a vehicle. Preferably high end vehicles such as Valtori, Castellverde and Morvani but I will also happily work on any car, truck or suv no matter what brand.

Industry/Entity Type

Automotive

Contact Information for Business Card

Bright Crest Detailing
Mira Tolland
4175 Quenhollow Rd
Ashmere PA 17492
Cell phone- call/text- 717-555-0148
email- brightcrestdetails@maildrop-example.com
Instagram: @brightcrestdetailing
Facebook: facebook.com/brightcrestdetailing

Requirements
Must have
• Business name, my name, address, phone number. Listing that I do minor paint correction such as clay barring, multi-step buffing and polishing, waxing, hand washes, interior cleaning, and more. (This last part was in nice to haves but I have realized that I do really want it, so I moved it to must haves.) I want something that is different and eye-catching to my customers. Some people have done this very well with cards already submitted to me, but a lot have not. I didn't mess with the "look and feel bars" much because because I am pretty open to the overall design as long as it is not your basic run of the mill design.
Nice to have
• Something car related. Maybe an appointment time/date line. I do not have a logo, but if you would like to design one and incorporate it, that would be amazing!
Should not have
• Purple and Pink colors. Boring, basic, normal card.

```html
<!DOCTYPE html>
<html lang="en">
<head>
<meta charset="utf-8">
<title>Bright Crest Detailing – Business Card</title>
<link rel="stylesheet" href="https://fonts.googleapis.com/css2?family=Arimo:wght@400&family=Tinos:wght@400&display=swap">
<style>
  :root {
    --canvas: #e9e7e3;
    --card-white: #f5f5f4;
    --teal: #10acb2;
    --teal-deep: #0a969c;
    --slate: #3b444a;
    --slate-deep: #2e363b;
    --ink: #151515;
    --ink-soft: #2a2a2a;
    --ink-muted: #4a5156;
    --on-dark: #ffffff;
    --edge-blue: #1f6fb0;
  }
  * { margin: 0; padding: 0; box-sizing: border-box; }
  html, body { width: 1200px; height: 892px; overflow: hidden; }
  body {
    background: var(--canvas);
    position: relative;
    font-family: "Arimo", Arial, sans-serif;
  }
  .card {
    position: absolute;
    width: 620px;
    height: 354px;
    background: var(--card-white);
    overflow: hidden;
    box-shadow: 0 10px 24px rgba(0,0,0,0.18);
  }
  .card-front { left: 290px; top: 64px; border-bottom: 4px solid var(--teal-deep); }
  .card-back { left: 290px; top: 474px; border-bottom: 4px solid var(--edge-blue); }
  .card-shape { position: absolute; inset: 0; width: 100%; height: 100%; }

  .front-title {
    position: absolute; left: 0; right: 0; top: 40px;
    text-align: center; font-size: 33px; font-weight: 400; color: var(--ink);
  }
  .front-name {
    position: absolute; left: 0; right: 0; top: 112px;
    text-align: center; font-size: 24px; font-weight: 400; color: var(--ink-soft);
  }
  .contact-list {
    position: absolute; left: 228px; top: 200px;
    list-style: none; color: var(--on-dark); font-size: 17px; line-height: 23px;
  }
  .social-row {
    position: absolute; left: 222px; top: 308px; display: flex; gap: 22px;
  }
  .social-dot { width: 13px; height: 13px; background: var(--on-dark); opacity: 0.92; }

  .back-title {
    position: absolute; right: 60px; top: 40px;
    font-family: "Tinos", "Times New Roman", serif; font-size: 38px; font-weight: 400; color: var(--ink);
  }
  .back-name {
    position: absolute; right: 150px; top: 92px; font-size: 23px; font-weight: 400; color: var(--ink-soft);
  }
  .service-heading {
    position: absolute; left: 40px; top: 138px;
    font-size: 13px; letter-spacing: 2px; text-transform: uppercase; color: var(--teal-deep);
  }
  .service-list {
    position: absolute; left: 40px; top: 160px; width: 540px;
    list-style: none; display: flex; flex-wrap: wrap; gap: 4px 18px;
    font-size: 14px; line-height: 18px; color: var(--ink-muted);
  }
  .service-list li::before { content: "✓ "; color: var(--teal-deep); }
  .appointment {
    position: absolute; left: 40px; top: 212px; font-size: 13px; color: var(--ink-muted);
  }
  .appointment .blank {
    display: inline-block; width: 90px; border-bottom: 1px solid var(--ink-muted); margin: 0 8px 0 4px;
  }
  .back-handle {
    position: absolute; left: 28px; top: 266px; font-size: 16px; color: var(--on-dark);
  }
  .back-email {
    position: absolute; left: 150px; top: 306px; font-size: 17px; color: var(--on-dark);
  }
</style>
</head>
<body>

<section class="card card-front" aria-label="Business card front">
  <svg class="card-shape" viewBox="0 0 620 354" preserveAspectRatio="none" aria-hidden="true">
    <defs>
      <linearGradient id="tealBody" x1="0" y1="0" x2="1" y2="1">
        <stop offset="0" stop-color="#0fb4ba"/>
        <stop offset="1" stop-color="#0a9aa0"/>
      </linearGradient>
    </defs>
    <rect width="620" height="354" fill="url(#tealBody)"/>
    <path d="M0 0H620V96H478Q462 96 460 114Q455 176 400 180H220Q165 176 160 114Q158 96 142 96H0Z" fill="#f5f5f4"/>
  </svg>
  <h1 class="front-title">Bright Crest Detailing</h1>
  <p class="front-name">Mira Tolland</p>
  <ul class="contact-list">
    <li>717-555-0148</li>
    <li>@brightcrestdetailing</li>
    <li>brightcrestdetails@maildrop-example.com</li>
    <li>4175 Quenhollow Rd,Ashmere PA 17492</li>
  </ul>
  <div class="social-row" aria-hidden="true">
    <span class="social-dot"></span><span class="social-dot"></span>
    <span class="social-dot"></span><span class="social-dot"></span>
  </div>
</section>

<section class="card card-back" aria-label="Business card back">
  <svg class="card-shape" viewBox="0 0 620 354" preserveAspectRatio="none" aria-hidden="true">
    <defs>
      <linearGradient id="slateBand" x1="0" y1="0" x2="0" y2="1">
        <stop offset="0" stop-color="#414b51"/>
        <stop offset="1" stop-color="#2e363b"/>
      </linearGradient>
    </defs>
    <path d="M0 244H548L500 354H0Z" fill="url(#slateBand)"/>
  </svg>
  <h2 class="back-title">Bright Crest Detailing</h2>
  <p class="back-name">Mira Tolland</p>
  <p class="service-heading">Auto Detailing &amp; Minor Paint Correction</p>
  <ul class="service-list">
    <li>Clay Barring</li>
    <li>Multi-Step Buffing &amp; Polishing</li>
    <li>Waxing</li>
    <li>Hand Washes</li>
    <li>Interior Cleaning</li>
    <li>And More</li>
  </ul>
  <p class="appointment">Appointment: Date<span class="blank"></span>Time<span class="blank"></span></p>
  <p class="back-handle">@brightcrestdetailing</p>
  <p class="back-email">brightcrestdetails@maildrop-example.com</p>
</section>

</body>
</html>
```